Hurricane Damage Public Adjuster Billboard

I have created several projects with you and have several great designs. I need to format them into a Billboard for upcoming Hurricane Season. Need done in a month. Im also in process of getting an eye catching and easy to remember 800# Vanity phone number like Call 800-Stormsafe or 800- Need Fix? My included past Craft Huddle projects will give you an idea of what colors, schemes, and designs I gravitate towards. 3 past Design projects were 1) 2 Logos where I picked the 1st place and the 2nd place and 2) Index Card where I picked the winner as the Index Card and the 2nd place as a Post Card. Point is, I will pick and pay for 2 winners if they're good. This should help to sweeten the pot. Also, please look at my website for ideas that I like:

www.TheClaimKeeperGroup.com
I want people to feel that I am the best and highest. Level.

I've been getting a lot of quick half effort designs basically cut & pasting my previous projects. Please don't rush and take your time to be creative. A an example, my Biggest Competitor is Vesta Public Adjusting. Their colors are Black and Gold while mine are Blue, White, and Black with a highlight of Orange if possible. I JUST imported a picture of their BillBoard. I need mine better and BLOW AWAY THEIRS. Terms like "Don't be Victimized Twice ?, Don't let the Hurricane Ruin your Life?". "Get Fairly Paid & Move On" "Our Clients Claims are VIP?
Updates

I'm getting a lot of quick half effort ones. I'd rather you take your time and really put some thoughts and effort into it. My Biggest Competitor is Vesta Public Adjusting. They have black & gold colors, while I have Blue, Black, and white.

It needs to blow theirs away. I have imported their Billboard for comparative purposes.

Guy's,
I'll make it easier for you in what I'm looking for. Please look at the Vesta Billboard picture attached.

1) Put my "Blue Shield" to the left, replacing their logo
2) change color patterns from their (Black, Gold, White) to my color schemes of (Black, Blue, White)
3) I want to see my name where their is:

THE
Claim Keeper's Group
EXPERT & LOCAL Public Adjusters
"FOR THE POLICYHOLDER!!"

4) to the right, add the A+Rated logo and QRS+ Accredited logo, 5 Star Zorbix Rated logo, 5 Start PORCHLINE Highly Rated logo, etc..

5) the right side is where you can be creative as I will not have a picture of me there.

"20+ Years of Experience, Recovering Millions for our VIP Clients"

"Your Best, Locally-Based Private Adjuster & Advocate'
"FOR THE POLICYHOLDER!!"

"Don't be victimized Twice!!"

"Don't let the Hurricane Ruin Your Life!!"

This should really help. Also, refer to my website, maybe a couple testimonial fillers?

Thanks all,

marcus@TheClaimKeeperGroup.com

Just imported a few awards that would look great to the right side with all the other 5 Star Ratings and accolades.
This right section could be titled like zmy Website:

5 Star Reviews, Ratings & Awards:
4-5 Logos underneath?

Target Market(s)

Coastal place where a Hurricane 🌀 🌀 Hits

Industry/Entity Type

Hurricane Public Insurance Adjuster

Font styles to use
Sans Serif
Other font styles liked:
• Zurich fonts

Colors
0054AA
0677BA
7BADD7
CADEEF
E8F1F8
EE7325
F08F49
F5BC92
FAE3D3
FDF4ED

Requirements
Must have
• Use my past project logos, colors, and schemes to create eye grabbing BillBoard
Nice to have
Should not have
• Not be too busy, must be Easy to Read, Eye Catchy

```html
<!DOCTYPE html>
<html lang="en">
<head>
<meta charset="utf-8">
<title>The Claim Keeper's Group – Hurricane Billboard</title>
<link rel="stylesheet" href="https://fonts.googleapis.com/css2?family=Cinzel:wght@400;700&family=Poppins:ital,wght@0,600;0,700;0,800;1,800&family=Noto+Serif:wght@400&display=swap">
<style>
  :root{
    --page:#eef1f4;
    --navy:#1e2532;
    --navy-deep:#171c26;
    --storm-red:#b8453a;
    --storm-rust:#8a3a3c;
    --brand-blue:#0a8fe0;
    --white:#ffffff;
    --black:#000000;
    --orange:#f7931e;
    --headline-orange:#ff8a00;
    --alert-red:#ed1c24;
    --badge-gold:#f2b233;
    --badge-blue:#0b5aa6;
  }
  *{box-sizing:border-box;margin:0;padding:0}
  html,body{width:1200px;height:545px;overflow:hidden;background:var(--page)}
  .billboard{
    position:absolute;left:20px;top:107px;width:1160px;height:330px;overflow:hidden;
    font-family:"Poppins",sans-serif;color:var(--white);
  }
  .scene-art{
    position:absolute;inset:0;
    background:
      radial-gradient(ellipse 260px 120px at 780px 250px, rgba(190,150,120,.55), transparent 70%),
      linear-gradient(180deg,var(--navy) 0%,#2a2c3c 30%,var(--storm-rust) 52%,var(--storm-red) 66%,#4a3a36 78%,var(--navy-deep) 100%);
  }
  .shapes{position:absolute;inset:0}
  .brand-mark{
    position:absolute;left:48px;top:96px;width:216px;
    text-align:center;color:var(--brand-blue);
    font-weight:800;font-size:27px;line-height:1.12;letter-spacing:.5px;
  }
  .title{position:absolute;left:260px;width:510px;text-align:center;white-space:nowrap}
  .title-top{
    top:58px;font-family:"Cinzel",serif;font-weight:700;font-size:33px;line-height:1;
    text-shadow:0 2px 3px rgba(0,0,0,.6);
  }
  .title-sub{
    top:90px;display:flex;align-items:center;justify-content:center;gap:10px;
    font-family:"Cinzel",serif;font-weight:400;font-size:33px;line-height:1;
  }
  .title-sub .rule{display:block;width:84px;height:2px;background:var(--white)}
  .tagline{top:128px;font-weight:600;font-size:19px;line-height:1;letter-spacing:.3px}
  .promise{top:159px;font-weight:800;font-style:italic;font-size:22px;line-height:1;text-shadow:0 2px 3px rgba(0,0,0,.6)}
  .rating-card{
    position:absolute;left:271px;top:232px;width:84px;height:38px;
    background:var(--black);border:1.5px solid var(--alert-red);border-radius:4px;
    text-align:center;padding-top:1px;white-space:nowrap;
  }
  .rating-card .grade{font-weight:700;font-size:13.5px;line-height:15px}
  .rating-card .note{font-family:"Noto Serif",serif;font-size:5.2px;line-height:5.8px}
  .listing-caption{
    position:absolute;left:412px;top:264px;width:94px;text-align:center;
    font-weight:600;font-size:7.5px;line-height:1;white-space:nowrap;
  }
  .phone{
    position:absolute;left:540px;top:226px;width:324px;text-align:center;
    font-weight:800;font-size:41px;line-height:52px;letter-spacing:0;white-space:nowrap;
  }
  .warning{position:absolute;left:864px;top:0;width:296px;height:330px;text-align:center}
  .warning .line{
    position:absolute;left:0;right:0;font-weight:800;line-height:1;white-space:nowrap;
    transform:scaleY(1.27);transform-origin:top center;
  }
  .line-dont{top:32px;font-size:54px;color:var(--alert-red)}
  .line-let{top:96px;font-size:33px;color:var(--headline-orange)}
  .line-hurricane{top:135px;font-size:39px;color:var(--alert-red)}
  .line-ruin{top:181px;font-size:51px;color:var(--headline-orange)}
  .line-life{top:240px;font-size:29px;color:var(--alert-red)}
</style>
</head>
<body>
<main class="billboard">
  <div class="scene-art" role="img" aria-label="Stormy sunset sky with lightning over a hurricane-damaged beach house"></div>

  <svg class="shapes" viewBox="0 0 1160 330" width="1160" height="330" aria-hidden="true">
    <polygon points="794,0 1160,0 1160,330 887,330" fill="var(--white)"/>
    <polygon points="801,0 1160,0 1160,330 894,330" fill="var(--black)"/>
    <polygon points="236,222 250,222 272,282 257,282" fill="var(--white)"/>
    <polygon points="250,222 514,222 533,282 272,282" fill="var(--orange)"/>
    <polygon points="514,222 862,222 879,282 533,282" fill="var(--alert-red)"/>
    <circle cx="385" cy="251" r="20" fill="var(--badge-gold)" stroke="var(--white)" stroke-width="1.5"/>
    <rect x="412" y="230" width="94" height="32" rx="4" fill="var(--badge-blue)" stroke="var(--white)" stroke-width="1.5"/>
  </svg>

  <div class="brand-mark">CLAIM<br>KEEPER'S<br>GROUP</div>

  <h1 class="title title-top">THE CLAIM KEEPER'S</h1>
  <div class="title title-sub"><span class="rule"></span>GROUP<span class="rule"></span></div>
  <p class="title tagline">EXPERT &amp; LOCAL PUBLIC ADJUSTERS</p>
  <p class="title promise">FOR THE POLICYHOLDER!!</p>

  <div class="rating-card">
    <div class="grade">A+ Rating</div>
    <div class="note">Highest Rating For<br>Public Insurance Adjusters<br>(Source: ClaimRank's)</div>
  </div>
  <p class="listing-caption">QRS Rating: A+</p>

  <p class="phone">850-555-0148</p>

  <div class="warning">
    <span class="line line-dont">DON'T</span>
    <span class="line line-let">LET THE</span>
    <span class="line line-hurricane">HURRICANE</span>
    <span class="line line-ruin">RUIN</span>
    <span class="line line-life">YOUR LIFE!!</span>
  </div>
</main>
</body>
</html>
```